Business Card Design

I already have a company logo for my company. I have a logo for the manufacturer we represent. I want a professional business card design.

```html
<!DOCTYPE html>
<html lang="en">
<head>
<meta charset="utf-8">
<title>Business Card – Signalway Solutions</title>
<link rel="stylesheet" href="https://fonts.googleapis.com/css2?family=Open+Sans:wght@400;600;700&display=swap">
<style>
  :root {
    --backdrop: #222224;
    --card-black: #1e1d21;
    --gold: #b98c2d;
    --red: #e2202a;
    --white: #ffffff;
    --pattern-dark: #141416;
    --pattern-mid: #2a2a2e;
  }
  * { margin: 0; padding: 0; box-sizing: border-box; }
  html, body {
    width: 1200px; height: 780px; overflow: hidden;
    background: var(--backdrop);
    font-family: "Open Sans", Arial, sans-serif;
  }
  .canvas {
    width: 1200px; height: 780px;
    display: flex; align-items: center; justify-content: center; gap: 44px;
  }
  .card {
    position: relative;
    width: 540px; height: 310px;
    border-radius: 18px;
    overflow: hidden;
    box-shadow: 0 18px 40px rgba(0,0,0,.45);
  }
  .card-art { position: absolute; inset: 0; width: 100%; height: 100%; }

  /* front */
  .card-front { background: var(--gold); }
  .contact-block {
    position: absolute; left: 34px; top: 34px;
    color: var(--white);
  }
  .person-name { font-size: 24px; font-weight: 700; line-height: 1.1; color: var(--white); white-space: nowrap; }
  .person-name .first { color: var(--red); }
  .person-title { font-size: 14px; font-weight: 600; margin-top: 4px; }
  .address { font-size: 12.5px; line-height: 1.45; margin-top: 14px; }
  .contact-list { list-style: none; margin-top: 10px; font-size: 12.5px; line-height: 1.6; }
  .contact-list li { display: flex; align-items: center; gap: 8px; }
  .contact-icon { width: 12px; height: 12px; flex: none; }
  .contact-icon * { fill: none; stroke: var(--red); stroke-width: 1.8; stroke-linecap: round; stroke-linejoin: round; }

  .brand-front {
    position: absolute; right: 20px; top: 30px;
    display: flex; align-items: center; gap: 8px;
    color: var(--white);
    font-size: 14px; font-weight: 700; line-height: 1.15;
    text-transform: uppercase; letter-spacing: .03em;
  }
  .brand-dot { width: 18px; height: 18px; border-radius: 50%; background: var(--red); flex: none; }

  /* back */
  .card-back { background: var(--pattern-dark); }
  .pattern-field {
    position: absolute; inset: 0;
    background: linear-gradient(135deg, var(--pattern-dark) 0%, var(--pattern-mid) 55%, var(--pattern-dark) 100%);
  }
  .brand-back {
    position: absolute; right: 30px; bottom: 26px;
    color: var(--red);
    font-size: 11px; font-weight: 700;
    text-transform: uppercase; letter-spacing: .04em;
  }
</style>
</head>
<body>
<main class="canvas">

  <section class="card card-front" aria-label="Business card front">
    <svg class="card-art" viewBox="0 0 540 310" aria-hidden="true">
      <path d="M290 0 C352 0 364 95 386 178 C410 262 456 298 540 298 L540 0 Z" fill="var(--red)"/>
      <path d="M306 0 C364 0 376 88 398 166 C420 246 462 276 540 276 L540 0 Z" fill="var(--card-black)"/>
      <path d="M282 10 C330 42 340 130 362 200 C382 262 420 292 470 310" fill="none" stroke="var(--card-black)" stroke-width="2"/>
      <path d="M286 60 C318 100 326 160 344 214 C362 266 392 294 430 310" fill="none" stroke="var(--card-black)" stroke-width="1.1"/>
    </svg>

    <div class="contact-block">
      <h1 class="person-name"><span class="first">Marta</span> Kovalenko</h1>
      <p class="person-title">Managing Director</p>
      <p class="address">1840 Lakeside Ave. Suite 310<br>Denton, TX 76201</p>
      <ul class="contact-list">
        <li>
          <svg class="contact-icon" viewBox="0 0 12 12"><path d="M2.5 1.5 L4.5 1.5 L5.2 4 L3.9 4.9 C4.5 6.3 5.7 7.5 7.1 8.1 L8 6.8 L10.5 7.5 L10.5 9.5 C10.5 10.1 10 10.5 9.4 10.5 C5.3 10.2 1.8 6.7 1.5 2.6 C1.5 2 1.9 1.5 2.5 1.5 Z"/></svg>
          (940) 555-0184
        </li>
        <li>
          <svg class="contact-icon" viewBox="0 0 12 12"><rect x="1" y="2.5" width="10" height="7" rx="1"/><path d="M1.5 3 L6 6.5 L10.5 3"/></svg>
          info@signalway.com
        </li>
        <li>
          <svg class="contact-icon" viewBox="0 0 12 12"><circle cx="6" cy="6" r="4.8"/><path d="M1.2 6 H10.8 M6 1.2 C3.8 4 3.8 8 6 10.8 M6 1.2 C8.2 4 8.2 8 6 10.8"/></svg>
          www.signalway.com
        </li>
      </ul>
    </div>

    <div class="brand-front">
      <span class="brand-dot" aria-hidden="true"></span>
      <span>Signalway<br>Solutions LLC</span>
    </div>
  </section>

  <section class="card card-back" aria-label="Business card back">
    <div class="pattern-field" role="img" aria-label="Repeating tone-on-tone company mark pattern across a black field"></div>
    <p class="brand-back">Signalway Solutions</p>
  </section>

</main>
</body>
</html>
```